Wordpress Powered Website. Outstanding Design Required. Using Morvenic Theme

Designers will not need to create anything other than the home page but there are some design elements on the home page which also need to be factored in: 6 product place holders and 2-3 slides for a slideshow (with images I provide).

Designers will need to familiarise themselves with the Morvenic theme to make sure that their design will work within the theme.

The winning designer will set up all the pages and navigation in place. This includes social media icons, favicon, widgets, etc. In other words, the home page needs to be designed and coded and the other preset theme pages need to be organised in a way that we can start using the website on completion of the job.

Most of the designs I had last time were too colourful. This needs to be subtle not in your face.

Background to the business/website:
Ridgeway Banners is a new Australian venture which will sell large format printed banners and other signage. The market is very competitive so it is important to stand out visually and to have a website which is clean, easy to navigate and easy to order. It will be a combination of online sales and assisted sales but all sales enquiries will come from the website.

As our business is focused on presentation it is vital to have excellent design.
Purchased theme is Morvenic. Only this theme is to be used.

1. A home page using all the preset features of the Morvenic theme - it will just be basically taking my wireframe and inputting it to the live theme.
2. A three slide slideshow, ideally with an edited video. The static image slides can be provided by me during the handover. Placeholder for now.
Similar to this one: http://thecedarhollow.example.au/

Attached is the logo which must be utilised, although it could also sit on a dark background. There is our mascot as well which can be used but does not have to be included.

Target Market(s)

Primarily B2B (business to business)
Main industries will be Construction, Retail, Community, Events & Trade Shows

Industry/Entity Type

Printing

Coding

Coded - Design and coding required

Font styles to use
Sans Serif

Requirements
Must have
• Must have the design files made to web pages within the Wordpress environment.
Nice to have
• Clean design. Stand out from competitors based on design.
Should not have
• Should not look like any competitor

```html
<!DOCTYPE html>
<html lang="en">
<head>
<meta charset="utf-8">
<title>Ridgeway Banners</title>
<link href="https://fonts.googleapis.com/css2?family=Montserrat:wght@300;400;600;700&family=Open+Sans:wght@400;600&display=swap" rel="stylesheet">
<style>
:root{
  --green:#8cc63f;
  --blue:#1d86d4;
  --ink:#333;
  --muted:#8a8a8a;
  --light:#f0f0f0;
  --footer:#1d1d1d;
  --footer-text:#b5b5b5;
  --white:#fff;
}
*{margin:0;padding:0;box-sizing:border-box}
html,body{width:1200px;height:2188px;overflow:hidden;background:var(--white)}
body{position:relative;font-family:"Open Sans",Arial,sans-serif;color:var(--ink)}

/* header */
.site-header{position:absolute;top:0;left:0;width:1200px;height:80px;border-bottom:1px solid #e4e4e4;background:var(--white)}
.brand{position:absolute;left:100px;top:24px;display:flex;align-items:center;gap:10px;font-family:"Montserrat",Arial,sans-serif;font-weight:700;font-size:22px;color:var(--blue)}
.brand-mark{width:22px;height:22px;background:var(--green)}
.main-nav{position:absolute;right:100px;top:31px;display:flex;gap:26px;list-style:none;font-family:"Montserrat",Arial,sans-serif;font-size:11px;letter-spacing:.5px}
.main-nav li{color:#666}
.main-nav .active{color:var(--green);border-bottom:2px solid var(--green);padding-bottom:6px}

/* hero */
.hero{position:absolute;top:81px;left:0;width:1200px;height:410px;overflow:hidden}
.hero-wash{position:absolute;inset:0;background:
  radial-gradient(ellipse 420px 120px at 300px 330px,rgba(140,198,63,.22),transparent 70%),
  radial-gradient(ellipse 520px 140px at 900px 350px,rgba(29,134,212,.22),transparent 70%),
  radial-gradient(ellipse 360px 110px at 620px 380px,rgba(240,120,170,.18),transparent 70%),
  linear-gradient(#fff,#fbfbfb)}
.hero-title{position:absolute;left:100px;top:160px;font-family:"Montserrat",Arial,sans-serif;font-weight:400;font-size:26px;line-height:36px;color:#222}
.hero-collage{position:absolute;left:420px;top:0;width:520px;height:330px}
.hero-rule{position:absolute;top:491px;left:0;width:1200px;height:3px;background:linear-gradient(90deg,var(--green),var(--blue))}

/* welcome */
.welcome{position:absolute;top:540px;left:0;width:1200px;text-align:center}
.section-title{font-family:"Montserrat",Arial,sans-serif;font-weight:400;font-size:30px;color:#444}
.section-title .accent{color:var(--blue)}
.welcome p{width:960px;margin:26px auto 0;font-size:12.5px;line-height:23px;color:var(--muted)}

/* products */
.products{position:absolute;top:800px;left:0;width:1200px;height:520px}
.products-bg{position:absolute;inset:0;background:linear-gradient(180deg,#6e6e6e 0%,#9a9a9a 45%,#bdbdbd 100%)}
.products .section-title{position:absolute;top:30px;width:100%;text-align:center;color:var(--white)}
.product-card{position:absolute;background:var(--white);padding:8px;box-shadow:0 2px 6px rgba(0,0,0,.25)}
.product-card .thumb{width:100%;height:100%}
.view-all{position:absolute;left:565px;top:468px;width:70px;height:22px;border:1px solid #ddd;background:rgba(0,0,0,.45);color:var(--white);font-size:10px;line-height:20px;text-align:center;font-family:"Montserrat",Arial,sans-serif}

/* testimonials */
.testimonials{position:absolute;top:1335px;left:0;width:1200px}
.testimonials .section-title{text-align:center}
.quote{position:absolute;top:100px;width:470px;height:112px;background:var(--light);border-radius:6px;padding:18px 24px 0 80px;font-size:12px;line-height:21px;color:var(--muted)}
.quote::before{content:"\201C";position:absolute;left:22px;top:-6px;font-family:Georgia,serif;font-size:72px;color:#a9d0ee}
.quote::after{content:"";position:absolute;left:60px;bottom:-10px;border:10px solid transparent;border-top-color:var(--light);border-bottom:0}
.avatar{position:absolute;top:228px;width:50px;height:50px;border-radius:50%;background:linear-gradient(#c9b9a3,#8d7c68)}
.client-name{position:absolute;top:266px;font-family:"Montserrat",Arial,sans-serif;font-size:11.5px;font-weight:600;color:var(--blue)}
.dots{position:absolute;top:355px;left:585px;display:flex;gap:5px}
.dots span{width:6px;height:6px;border-radius:50%;background:#ccc}
.dots .on{background:var(--blue)}

/* footer */
.footer-wave{position:absolute;top:1690px;left:0;width:1200px;height:100px}
.site-footer{position:absolute;top:1788px;left:0;width:1200px;height:362px;background:var(--footer);color:var(--footer-text);font-size:11px}
.footer-col{position:absolute;top:70px}
.footer-col h4{font-family:"Montserrat",Arial,sans-serif;font-size:12px;font-weight:700;color:var(--white);letter-spacing:.5px;margin-bottom:18px}
.footer-col h4 .accent{color:var(--green)}
.links{list-style:none;line-height:24px}
.links li::before{content:"\203A";margin-right:6px;color:var(--green)}
.contact-name{color:var(--white);font-weight:600;margin-bottom:4px}
.contact-row{display:flex;align-items:center;gap:8px;margin-top:14px}
.field{width:200px;height:24px;border:1px solid #444;background:#111;margin-bottom:10px;padding:0 8px;line-height:22px;color:#888;font-size:10px}
.subscribe{width:200px;height:24px;background:var(--green);color:var(--white);text-align:center;line-height:24px;font-size:10px;font-family:"Montserrat",Arial,sans-serif;letter-spacing:.5px}
.social{display:flex;align-items:center;gap:10px;margin-bottom:12px}
.social-dot{width:22px;height:22px;border-radius:50%;background:var(--blue)}
.social strong{display:block;color:var(--white);font-size:10px;font-weight:600}
.social small{font-size:9px}
.copyright{position:absolute;top:2150px;left:0;width:1200px;height:38px;background:var(--blue);color:var(--white);font-size:10px;text-align:center;line-height:38px}
</style>
</head>
<body>

<header class="site-header">
  <div class="brand"><span class="brand-mark"></span>Ridgeway Banners</div>
  <ul class="main-nav">
    <li class="active">HOME</li><li>ABOUT US</li><li>PRODUCT</li><li>CATEGORY</li><li>FAQS</li><li>CONTACT US</li>
  </ul>
</header>

<section class="hero">
  <div class="hero-wash" role="img" aria-label="Soft colourful light swirls across a white background"></div>
  <h1 class="hero-title">A selection of Creative<br>Commissioned Works.</h1>
  <svg class="hero-collage" viewBox="0 0 520 330" role="img" aria-label="Diamond collage of printed banner and signage project photos">
    <g stroke="#fff" stroke-width="3">
      <polygon points="210,10 260,60 210,110 160,60" fill="#c9c9c9"/>
      <polygon points="310,10 360,60 310,110 260,60" fill="#9fb6c9"/>
      <polygon points="110,60 160,110 110,160 60,110" fill="#bfc7cf"/>
      <polygon points="210,110 260,160 210,210 160,160" fill="#d7b98f"/>
      <polygon points="310,110 360,160 310,210 260,160" fill="#8e9aa6"/>
      <polygon points="410,60 460,110 410,160 360,110" fill="#d9dde2"/>
      <polygon points="160,160 210,210 160,260 110,210" fill="#e0a36e"/>
      <polygon points="260,160 310,210 260,260 210,210" fill="#7f8c99"/>
      <polygon points="360,160 410,210 360,260 310,210" fill="#b9c4ce"/>
      <polygon points="460,160 505,205 460,250 415,205" fill="#cfd6dc"/>
      <polygon points="60,160 105,205 60,250 15,205" fill="#d4d4d4"/>
      <polygon points="210,250 250,290 210,330 170,290" fill="#a8b3bd"/>
      <polygon points="310,250 350,290 310,330 270,290" fill="#c4ccd3"/>
    </g>
  </svg>
</section>
<div class="hero-rule"></div>

<section class="welcome">
  <h2 class="section-title">Welcome To Ridgeway Banners</h2>
  <p>Ridgeway Banners prints large format banners, pull-up stands, flags and signage for builders, retailers, community groups and event organisers across Australia. Every job is checked by a designer before it reaches the press, so colours stay true and edges stay crisp. Order online in a few steps or talk with our team for help choosing sizes, materials and finishes. We turn artwork around quickly, pack it with care and deliver it ready to hang, so your brand looks sharp on the site fence, the shop window or the trade show floor. Read more [...]</p>
</section>

<section class="products">
  <div class="products-bg" role="img" aria-label="Blurred photo of pull-up banner stands in a showroom"></div>
  <h2 class="section-title">Our Product</h2>
  <div class="product-card" style="left:205px;top:88px;width:190px;height:130px"><div class="thumb" role="img" aria-label="Product photo of a horizontal printed banner" style="background:linear-gradient(135deg,#2b2b2b,#b0542a)"></div></div>
  <div class="product-card" style="left:205px;top:258px;width:190px;height:160px"><div class="thumb" role="img" aria-label="Product photo of printed boxes and packaging" style="background:linear-gradient(135deg,#e9eef3,#5fb3e0)"></div></div>
  <div class="product-card" style="left:432px;top:88px;width:340px;height:345px"><div class="thumb" role="img" aria-label="Product photo of a pull-up banner stand" style="background:linear-gradient(160deg,#f2f2f2,#c9d6e4 60%,#9ab1c7)"></div></div>
  <div class="product-card" style="left:805px;top:100px;width:190px;height:110px"><div class="thumb" role="img" aria-label="Product photo of a printed business card" style="background:linear-gradient(135deg,#efe6d2,#d8c8a4)"></div></div>
  <div class="product-card" style="left:805px;top:268px;width:190px;height:150px"><div class="thumb" role="img" aria-label="Product photo of a green outdoor sign board" style="background:linear-gradient(135deg,#2f6b3e,#6fa65a)"></div></div>
  <div class="view-all">View All</div>
</section>

<section class="testimonials">
  <h2 class="section-title">Clients <span class="accent">Testimonials</span></h2>
  <div class="quote" style="left:100px">The pull-up banners arrived two days early and the colours matched our brand guide exactly. Ordering was simple and the team answered every question quickly.</div>
  <div class="quote" style="left:630px">Our site fence mesh still looks new after a wet winter. Clear pricing, friendly advice and a finish that made our project stand out on the street.</div>
  <div class="avatar" style="left:135px" role="img" aria-label="Client portrait"></div>
  <div class="avatar" style="left:665px" role="img" aria-label="Client portrait"></div>
  <div class="client-name" style="left:440px">Tova Linden Reyes</div>
  <div class="client-name" style="left:970px">Tova Linden Reyes</div>
  <div class="dots"><span class="on"></span><span></span><span></span></div>
</section>

<svg class="footer-wave" viewBox="0 0 1200 100" preserveAspectRatio="none" aria-hidden="true">
  <path d="M0 98 C300 98 700 96 900 60 C1020 38 1110 12 1200 0 L1200 100 L0 100 Z" fill="#1d86d4"/>
  <path d="M0 100 C320 100 720 100 920 72 C1040 54 1120 30 1200 18 L1200 100 Z" fill="#1d1d1d"/>
</svg>

<footer class="site-footer">
  <div class="footer-col" style="left:100px">
    <h4>QUICK <span class="accent">LINKS</span></h4>
    <ul class="links"><li>Home</li><li>About us</li><li>Product</li><li>Category</li><li>FAQs</li><li>Contact us</li></ul>
  </div>
  <div class="footer-col" style="left:300px;width:230px">
    <h4>CONTACT <span class="accent">INFORMATION</span></h4>
    <div class="contact-name">RIDGEWAY BANNERS</div>
    <div>Unit 4, 18 Kestrel Road, Ballarat VIC</div>
    <div class="contact-row"><svg width="12" height="12" viewBox="0 0 12 12"><path d="M2 1h2l1 3-1.5 1a6 6 0 0 0 3 3L7.5 6.5l3 1v2a1 1 0 0 1-1 1A9 9 0 0 1 1 2a1 1 0 0 1 1-1z" fill="#8cc63f"/></svg>+61 3 5550 1842</div>
    <div class="contact-row"><svg width="12" height="12" viewBox="0 0 12 12"><path d="M2 1h2l1 3-1.5 1a6 6 0 0 0 3 3L7.5 6.5l3 1v2a1 1 0 0 1-1 1A9 9 0 0 1 1 2a1 1 0 0 1 1-1z" fill="#8cc63f"/></svg>+61 3 5550 1843</div>
    <div class="contact-row"><svg width="12" height="10" viewBox="0 0 12 10"><rect x=".5" y=".5" width="11" height="9" fill="none" stroke="#8cc63f"/><path d="M.5.5 6 5.5 11.5.5" fill="none" stroke="#8cc63f"/></svg>info@ridgewaybanners.example.au</div>
  </div>
  <div class="footer-col" style="left:585px">
    <h4>NEWSLETTER <span class="accent">SIGNUP</span></h4>
    <div class="field">Name</div>
    <div class="field">Email</div>
    <div class="subscribe">SUBSCRIBE</div>
  </div>
  <div class="footer-col" style="left:955px">
    <h4>FOLLOW <span class="accent">US</span></h4>
    <div class="social"><span class="social-dot"></span><div><strong>NOTICEBOARD</strong><small>2.4k likes</small></div></div>
    <div class="social"><span class="social-dot"></span><div><strong>TRADE CIRCLE</strong><small>180 followers</small></div></div>
    <div class="social"><span class="social-dot"></span><div><strong>QUICKPOST</strong><small>960 followers</small></div></div>
  </div>
</footer>
<div class="copyright">© 2024 RIDGEWAY BANNERS. All Rights Reserved.</div>

</body>
</html>
```